Korrabel Ice Creamery tourist signage

We need to give passing tourists a snapshot of what great fun they can have visiting our brand new Ice creamery located in Timboon, 17km North of the Great Ocean Road and Famous 12 Apostles in Victoria Australia. So the sign needs to be more than directional, need to be enticing. needs to be designed in a manner that project quality. ( keep in mind cars travelling at 80km don't have a lot of time to read too much)
Size is 2.2metres wide by 1.4 meters high
This sign needs to be succinct. Needs to convey fun and a little indulgence but not in a 'tacky' or 'cheap' way.
Needs to offer indulgent imagery of course, our logo too and direction.

Target Market(s)

Tourists, domestic and internationals

Industry/Entity Type

Tourism

Font styles to use
Other font styles liked:
• sacred cow

Colors
add136
fdf3f8
b8a6cd
fabb94
fcca95
85acd3
fbf289

Requirements
Must have
• Convey fun, whimsy indulgence and value ( keeping in mind we need to entice these people a further 17km up the road!)
Nice to have
• White space and clear imagery with
Should not have
• Bold bling colours, be busy looking and cheap looking, needs to convey quality .

```html
<!DOCTYPE html>
<html lang="en">
<head>
<meta charset="utf-8">
<title>Korrabel Ice Creamery – Road Sign</title>
<link href="https://fonts.googleapis.com/css2?family=Baloo+2:wght@800&display=swap" rel="stylesheet">
<style>
  :root {
    --backdrop: #e6e4e8;
    --sign-white: #f3f3f3;
    --band-green: #add136;
    --band-yellow: #fbf289;
    --brand-green: #7fbf1f;
    --ink: #2b2b2b;
    --arrow-purple: #7a1fc7;
    --arrow-light: #9b2cf0;
    --scoop-pink: #f2bfd9;
    --scoop-cream: #f8f6f0;
    --scoop-brown: #9c8066;
    --scoop-mint: #b5e28f;
    --scoop-shadow: #d9cfc6;
  }
  html, body {
    margin: 0;
    padding: 0;
    width: 1200px;
    height: 886px;
    overflow: hidden;
    background: var(--backdrop);
  }
  .canvas {
    position: relative;
    width: 1200px;
    height: 886px;
  }
  .sign {
    position: absolute;
    left: 36px;
    top: 85px;
    width: 1127px;
    height: 716px;
    overflow: hidden;
    background: var(--sign-white);
    box-shadow: 0 6px 24px rgba(0,0,0,0.18);
  }
  .hero-photo {
    position: absolute;
    left: 0;
    top: 0;
    width: 1127px;
    height: 600px;
    background:
      radial-gradient(ellipse 230px 220px at 160px 440px, var(--scoop-brown) 0%, rgba(156,128,102,0.85) 55%, rgba(156,128,102,0) 100%),
      radial-gradient(ellipse 270px 250px at 860px 430px, var(--scoop-mint) 0%, rgba(181,226,143,0.9) 55%, rgba(181,226,143,0) 100%),
      radial-gradient(ellipse 230px 220px at 470px 190px, var(--scoop-cream) 0%, rgba(248,246,240,0.9) 55%, rgba(248,246,240,0) 100%),
      radial-gradient(ellipse 230px 200px at 950px 110px, var(--scoop-pink) 0%, rgba(242,191,217,0.9) 55%, rgba(242,191,217,0) 100%),
      radial-gradient(ellipse 200px 230px at 60px 180px, var(--scoop-pink) 0%, rgba(242,191,217,0.85) 55%, rgba(242,191,217,0) 100%),
      linear-gradient(135deg, var(--scoop-shadow), #e8dcd6 50%, #cfd8bf);
  }
  .sign-art {
    position: absolute;
    inset: 0;
    width: 100%;
    height: 100%;
  }
  .brand-name {
    position: absolute;
    left: 73px;
    top: 493px;
    width: 515px;
    margin: 0;
    text-align: center;
    white-space: nowrap;
    font-family: "Baloo 2", sans-serif;
    font-weight: 800;
    font-size: 104px;
    letter-spacing: 5px;
    line-height: 1;
    color: var(--ink);
  }
  .brand-tagline {
    position: absolute;
    left: 103px;
    top: 599px;
    width: 460px;
    margin: 0;
    text-align: center;
    white-space: nowrap;
    font-family: "Baloo 2", sans-serif;
    font-weight: 800;
    font-size: 54px;
    line-height: 1;
    color: var(--ink);
  }
  .distance {
    position: absolute;
    left: 703px;
    top: 608px;
    margin: 0;
    white-space: nowrap;
    font-family: "Baloo 2", sans-serif;
    font-weight: 800;
    font-size: 94px;
    letter-spacing: -3px;
    line-height: 1;
    color: var(--arrow-purple);
  }
</style>
</head>
<body>
<main class="canvas">
  <section class="sign">
    <div class="hero-photo" role="img" aria-label="Close-up photo of pink, vanilla, chocolate and mint ice cream scoops"></div>
    <svg class="sign-art" viewBox="0 0 1127 716" preserveAspectRatio="none">
      <path class="white-field" d="M0,498 Q520,640 1127,470 L1127,716 L0,716 Z" fill="var(--sign-white)"/>
      <path class="band-yellow" d="M460,583 Q820,590 1127,470 L1127,492 Q820,608 460,590 Z" fill="var(--band-yellow)"/>
      <path class="band-green" d="M0,496 Q560,650 1127,380 L1127,472 Q800,590 460,585 Q200,572 0,503 Z" fill="var(--band-green)"/>
      <circle class="brand-dot" cx="338" cy="575" r="110" fill="var(--brand-green)"/>
      <g class="direction-arrow">
        <polygon points="893,523 943,523 1028,620 943,716 893,716 978,620" fill="var(--arrow-purple)"/>
        <polygon points="963,523 1013,523 1098,620 1013,716 963,716 1048,620" fill="var(--arrow-light)"/>
      </g>
    </svg>
    <h1 class="brand-name">KORRABEL</h1>
    <p class="brand-tagline">* ICE CREAMERY *</p>
    <p class="distance">17km</p>
  </section>
</main>
</body>
</html>
```